Business card for Sports Apparel business

DOUBLE SIDED DESIGN
We need business cards for a new sports apparel business. We are developing a protective headband for soccer initially.
Torvalle is focused on designing and developing head protection products to reduce the likelihood of concussion when playing sports. Exploring and understanding medical insights, material science research, current and former players experiences and governing bodies guidelines has allowed Torvalle to develop the safety, style, form and function requirements of a suitable product to bring to market.
Target Market(s)
Mums buying kits for the sons and daughters. Amateur footballers.
Industry/Entity Type
Sporting Good
Contact Information for Business Card
Martin Ashworth - CEO
Mobile: +44 7431589027
Email: martin@torvalle.co.uk
Tel: 0208 5519372
Helena Pargeter - COO
Mob: +44 7385 640117
Email: helena@torvalle.co.uk
Tel: 0208 5519372
Duncan Farrow - CCO
Mob: +44 7564 293081
Email: duncan@torvalle.co.uk
Tel: 0208 5519372
Look and feel
Each slider illustrates characteristics of the customer's brand and the style your logo design should communicate.

```html
<!DOCTYPE html>
<html lang="en">
<head>
<meta charset="utf-8">
<title>Torvalle business card</title>
<link rel="stylesheet" href="https://fonts.googleapis.com/css2?family=Montserrat:wght@400;500;700&display=swap">
<style>
  :root {
    --bg: #1d1d1d;
    --card: #ffffff;
    --card-tint: #f1f2f4;
    --brand-blue: #1b5c9c;
    --ink: #1e1e22;
    --grass-light: #8fb33a;
    --grass-dark: #3f6a1c;
    --stadium-grey: #b9bcc0;
    --keeper-yellow: #e6d63a;
    --net-grey: #c9cdd2;
    --field-dark: #4a4f3c;
  }
  * { box-sizing: border-box; margin: 0; padding: 0; }
  html, body { width: 1200px; height: 900px; overflow: hidden; }
  body {
    background: var(--bg);
    font-family: "Montserrat", sans-serif;
    position: relative;
  }
  .card {
    position: absolute;
    top: 150px;
    width: 380px;
    height: 590px;
    background: linear-gradient(160deg, var(--card) 40%, var(--card-tint) 100%);
    overflow: hidden;
  }
  .card--front { left: 160px; }
  .card--back { left: 660px; }

  .photo {
    position: absolute;
    left: 0; top: 0;
    width: 100%;
    height: 300px;
    clip-path: polygon(0 0, 100% 0, 100% 92%, 90% 96%, 78% 91%, 64% 97%, 50% 90%, 36% 96%, 22% 88%, 10% 94%, 0 86%);
  }
  .photo--ball {
    background: linear-gradient(180deg, var(--stadium-grey) 0%, #8d9196 32%, var(--grass-light) 55%, var(--grass-dark) 100%);
  }
  .photo--keeper {
    background: linear-gradient(135deg, var(--net-grey) 0%, #9aa096 35%, var(--keeper-yellow) 62%, var(--field-dark) 100%);
  }

  .brand {
    position: absolute;
    left: 0; right: 0;
    top: 400px;
    display: flex;
    align-items: center;
    justify-content: center;
    gap: 14px;
  }
  .brand__mark {
    width: 22px; height: 22px;
    background: var(--brand-blue);
  }
  .brand__name {
    font-weight: 700;
    font-size: 40px;
    letter-spacing: 3px;
    color: var(--brand-blue);
    text-transform: uppercase;
  }

  .person {
    position: absolute;
    left: 0; right: 0;
    top: 326px;
    text-align: center;
  }
  .person__name {
    font-weight: 700;
    font-size: 27px;
    letter-spacing: 1px;
    color: var(--ink);
    text-transform: uppercase;
  }
  .person__role {
    font-weight: 500;
    font-size: 20px;
    color: var(--brand-blue);
    margin-top: 2px;
  }

  .contacts {
    position: absolute;
    left: 48px;
    top: 430px;
    list-style: none;
  }
  .contacts__item {
    display: flex;
    align-items: center;
    gap: 16px;
    height: 44px;
    font-size: 16px;
    color: var(--ink);
  }
  .contacts__icon {
    width: 28px; height: 28px;
    border-radius: 50%;
    background: var(--brand-blue);
    display: flex;
    align-items: center;
    justify-content: center;
    flex: none;
  }
</style>
</head>
<body>

<section class="card card--front">
  <div class="photo photo--ball" role="img" aria-label="Football resting on grass in a stadium"></div>
  <div class="brand">
    <span class="brand__mark"></span>
    <span class="brand__name">Torvalle</span>
  </div>
</section>

<section class="card card--back">
  <div class="photo photo--keeper" role="img" aria-label="Goalkeeper in yellow diving to save a ball in front of the net"></div>
  <div class="person">
    <h1 class="person__name">Duncan Farrow</h1>
    <p class="person__role">CCO</p>
  </div>
  <ul class="contacts">
    <li class="contacts__item">
      <span class="contacts__icon">
        <svg width="14" height="14" viewBox="0 0 24 24"><path fill="#fff" d="M6.6 10.8a15.1 15.1 0 0 0 6.6 6.6l2.2-2.2a1 1 0 0 1 1-.25 11.4 11.4 0 0 0 3.6.57 1 1 0 0 1 1 1V20a1 1 0 0 1-1 1A17 17 0 0 1 3 4a1 1 0 0 1 1-1h3.5a1 1 0 0 1 1 1c0 1.25.2 2.45.57 3.57a1 1 0 0 1-.25 1z"/></svg>
      </span>
      <span>+44 7564 293081</span>
    </li>
    <li class="contacts__item">
      <span class="contacts__icon">
        <svg width="14" height="14" viewBox="0 0 24 24"><rect x="3" y="6" width="18" height="12" fill="none" stroke="#fff" stroke-width="2"/><path d="M3 6l9 7 9-7" fill="none" stroke="#fff" stroke-width="2"/></svg>
      </span>
      <span>duncan@torvalle.co.uk</span>
    </li>
    <li class="contacts__item">
      <span class="contacts__icon">
        <svg width="14" height="14" viewBox="0 0 24 24"><path d="M3 9c0-3 18-3 18 0v2h-5V9H8v2H3z" fill="#fff"/><rect x="5" y="12" width="14" height="8" rx="1" fill="none" stroke="#fff" stroke-width="2"/><circle cx="12" cy="16" r="2" fill="#fff"/></svg>
      </span>
      <span>0208 5519372</span>
    </li>
  </ul>
</section>

</body>
</html>
```